Moxy Fen needs some awesome stationary

Do you have what it takes to get my brand? You either do or you don't, have a crack at a design and you my just win my business.

I don't want to waste your or my time, so put your creative genius on either a business card or envelope.

I however need a package of stationary that follows the same brand. I will message you to complete the remaining should I like your first submission.

Here is what I need, have a go!

Basically I need the following for my small business based in melbourne.
- Letterhead (printer ready and MS Word)
- Business Card
- Compliments Slip
- Envelope
- Proposal Cover Page (MS Word only)
- Presentation Folder
- Marbled Fox Cards
- Student Name Tent
- Index Cards
- Vell-Ka

I am establishing the brand and it must be modern, professional but also relaxed; that is not formal and not corporate. It represents a company are leaders, but small enough to care and operate like a bunch of friends. We are bringing people and conversations back to business, and turfing out all the bureaucracy and crazy and wasteful procedures. Its about "lets talk and figure it out together and find even better ways".

Target Market(s)

Mainly companies that build software products, but Agile practices are used in many other industries (even graphic design projects)

Industry/Entity Type

Information Technology

Font styles to use
Sans Serif

Colors
3176b5
aaaaaa

Requirements
Must have
• I like curves and circles and not boxes or rectangles.
• I want a colour rich design with my brand colours, but it must be balanced.
• I want more modern than traditional, but simple modern
Should not have
• Not corporate
• Please don't waste my time if your not going to think about it.
• Don't mess with my primary logo
• Don't change my colours
• Don't overlay logo on image

```html
<!DOCTYPE html>
<html lang="en">
<head>
<meta charset="utf-8">
<title>Moxy Fen – Notepad Page</title>
<link rel="stylesheet" href="https://fonts.googleapis.com/css2?family=Open+Sans:wght@700&display=swap">
<style>
  :root {
    --backdrop: #8a8b8f;
    --paper: #f1eff0;
    --brand-blue: #2f5f9e;
    --wash-blue: #dde1ea;
    --wash-grey: #e6e5e7;
    --rule-light: #b4b3b5;
    --rule-dark: #7d7c80;
  }
  html, body {
    margin: 0;
    padding: 0;
    overflow: hidden;
  }
  .canvas {
    position: relative;
    width: 1018px;
    height: 1200px;
    background: var(--backdrop);
    overflow: hidden;
  }
  .notepad-page {
    position: absolute;
    left: 210px;
    top: 204px;
    width: 598px;
    height: 768px;
    background: var(--paper);
    box-shadow: 0 1px 3px rgba(0, 0, 0, 0.25);
    overflow: hidden;
  }
  .page-wash {
    position: absolute;
    left: 0;
    top: 0;
    width: 598px;
    height: 768px;
  }
  .brand {
    position: absolute;
    left: 49px;
    top: 80px;
    display: flex;
    align-items: center;
    gap: 10px;
  }
  .brand-dot {
    width: 34px;
    height: 34px;
    border-radius: 50%;
    background: var(--brand-blue);
  }
  .brand-name {
    font-family: "Open Sans", sans-serif;
    font-weight: 700;
    font-size: 34px;
    line-height: 1;
    color: var(--brand-blue);
    letter-spacing: -0.3px;
  }
  .writing-lines {
    position: absolute;
    left: 40px;
    top: 0;
    width: 531px;
    height: 768px;
  }
  .writing-lines line {
    stroke-width: 1.3;
  }
  .rule-light { stroke: var(--rule-light); }
  .rule-dark { stroke: var(--rule-dark); }
</style>
</head>
<body>
  <div class="canvas">
    <section class="notepad-page">
      <svg class="page-wash" viewBox="0 0 598 768" role="img" aria-label="Soft circular brand-colour wash in the lower page">
        <defs>
          <linearGradient id="washTone" x1="0" y1="0" x2="1" y2="0">
            <stop offset="0" stop-color="var(--wash-blue)"/>
            <stop offset="1" stop-color="var(--wash-grey)"/>
          </linearGradient>
        </defs>
        <circle cx="300" cy="680" r="330" fill="url(#washTone)"/>
      </svg>
      <div class="brand">
        <span class="brand-dot"></span>
        <span class="brand-name">Moxy Fen</span>
      </div>
      <svg class="writing-lines" viewBox="0 0 531 768" aria-hidden="true">
        <line class="rule-light" x1="0" x2="531" y1="153" y2="153"/>
        <line class="rule-light" x1="0" x2="531" y1="197" y2="197"/>
        <line class="rule-light" x1="0" x2="531" y1="242" y2="242"/>
        <line class="rule-light" x1="0" x2="531" y1="287" y2="287"/>
        <line class="rule-dark" x1="0" x2="531" y1="333" y2="333"/>
        <line class="rule-dark" x1="0" x2="531" y1="369" y2="369"/>
        <line class="rule-dark" x1="0" x2="531" y1="414" y2="414"/>
        <line class="rule-dark" x1="0" x2="531" y1="459" y2="459"/>
        <line class="rule-dark" x1="0" x2="531" y1="504" y2="504"/>
        <line class="rule-dark" x1="0" x2="531" y1="549" y2="549"/>
        <line class="rule-dark" x1="0" x2="531" y1="594" y2="594"/>
        <line class="rule-dark" x1="0" x2="531" y1="630" y2="630"/>
        <line class="rule-dark" x1="0" x2="531" y1="675" y2="675"/>
        <line class="rule-dark" x1="0" x2="531" y1="720" y2="720"/>
      </svg>
    </section>
  </div>
</body>
</html>
```